Bright Harbor website redesign

We need a redesign for a website: mybrightharbor.example.

I already created a video going over what exactly is needed in the design.

See Video here: https://files.example.net/file/d/7xQpL2mR9vTz4KwB8nYcH3jDs6FgA1eU0/view?usp=sharing

Google Slide shown in Video: https://slides.example.net/presentation/d/9KP_Rtnwq3XbzmLeYc7VhJ2GoUd4Fs_PaiTe6q1kQ5Wr/edit?usp=sharing

Holidays in India so we did not get enough design entries or quality.

Target Market(s)

Dentistry

Industry/Entity Type

Dentistry

Number of Pages Required

1 page

Colors
0094D4
00A9DD
6FCCEA
C7EBF8
E9F6FB
00AB8E
00BBA5
67D7C9
C6EFE9
E9F9F6

Requirements
Must have
• See 13 min video link in description - shows what to do.

```html
<!DOCTYPE html>
<html lang="en">
<head>
<meta charset="utf-8">
<title>Bright Harbor – Dental Care</title>
<link rel="stylesheet" href="https://fonts.googleapis.com/css2?family=Montserrat:wght@400;500;600;700;800&family=Nunito+Sans:wght@400;600;700&display=swap">
<style>
:root{
  --blue-deep:#0094D4;
  --blue:#00A9DD;
  --blue-soft:#6FCCEA;
  --blue-pale:#C7EBF8;
  --blue-mist:#E9F6FB;
  --teal-deep:#00AB8E;
  --teal:#00BBA5;
  --teal-soft:#67D7C9;
  --teal-pale:#C6EFE9;
  --teal-mist:#E9F9F6;
  --ink:#2b4556;
  --text:#4d5b66;
  --green:#5aa83a;
  --white:#ffffff;
}
*{margin:0;padding:0;box-sizing:border-box}
html,body{width:1200px;height:4199px;overflow:hidden}
body{position:relative;background:var(--white);font-family:"Nunito Sans",Arial,sans-serif;color:var(--text)}

/* header */
.site-header{position:absolute;left:0;top:0;width:1200px;height:106px;background:var(--white)}
.brand{position:absolute;left:92px;top:30px;display:flex;align-items:center;gap:10px;font-family:"Montserrat",sans-serif;font-weight:700;font-size:26px;color:var(--teal-deep)}
.brand-dot{width:16px;height:16px;border-radius:50%;background:var(--teal)}
.phone{position:absolute;left:640px;top:15px;display:flex;align-items:center;gap:8px;font-size:17px;font-weight:600;color:var(--ink)}
.pill{position:absolute;top:8px;height:34px;border-radius:17px;color:var(--white);font-family:"Montserrat",sans-serif;font-weight:600;font-size:12px;display:flex;align-items:center;justify-content:center}
.pill.schedule{left:815px;width:145px;background:var(--teal)}
.pill.emergency{left:967px;width:143px;background:var(--blue)}
.main-nav{position:absolute;top:68px;left:0;font-size:13.5px;color:var(--text)}
.main-nav span{position:absolute;white-space:nowrap}
.nav-active-bar{position:absolute;left:314px;top:102px;width:78px;height:3px;background:var(--teal)}

/* hero */
.hero{position:absolute;left:0;top:106px;width:1200px;height:570px;background:linear-gradient(110deg,var(--blue) 0%,#05b3cf 45%,var(--teal) 100%)}
.hero-title{position:absolute;left:107px;top:140px;color:var(--white);font-family:"Montserrat",sans-serif;line-height:1.05}
.hero-title .light{font-size:50px;font-weight:400;display:block}
.hero-title .bold{font-size:48px;font-weight:800;display:block}
.hero-sub{position:absolute;left:112px;top:258px;color:var(--white);font-size:22px;font-weight:600;line-height:1.15}
.outline-btn{position:absolute;border:2px solid var(--white);color:var(--white);font-family:"Montserrat",sans-serif;font-weight:700;font-size:13px;display:flex;align-items:center;justify-content:center;border-radius:3px}
.hero .outline-btn{left:112px;top:331px;width:238px;height:54px}
.hero-art{position:absolute;left:530px;top:70px;width:630px;height:470px;border-radius:40px;background:radial-gradient(ellipse at 40% 45%,rgba(255,255,255,.32),rgba(255,255,255,.06) 70%)}

/* section heading */
.section-title{position:absolute;left:0;width:1200px;text-align:center;font-family:"Montserrat",sans-serif;font-size:30px;color:var(--ink);letter-spacing:.5px}
.section-title b{font-weight:700}
.section-title span{font-weight:400}
.title-rule{position:absolute;left:565px;width:70px;height:2px;background:var(--teal)}

/* team */
.member{position:absolute;top:838px;width:290px;text-align:center}
.portrait{width:285px;height:285px;border-radius:50%;margin:0 auto;background:linear-gradient(180deg,#eef1f3,#cfd6dc)}
.portrait.active{background:linear-gradient(180deg,var(--teal-soft),var(--teal));border:4px solid var(--teal-soft)}
.member h3{margin-top:25px;font-size:19px;font-weight:700;color:var(--ink)}
.member p{margin-top:6px;font-size:16px;font-weight:600;color:var(--green)}

/* bio band */
.bio-band{position:absolute;left:0;top:1272px;width:1200px;height:439px;background:linear-gradient(180deg,var(--teal) 0%,#06b2c0 55%,var(--blue) 100%)}
.bio-pointer{position:absolute;left:578px;top:1250px;width:0;height:0;border-left:22px solid transparent;border-right:22px solid transparent;border-bottom:22px solid var(--teal)}
.bio-text{position:absolute;left:165px;top:74px;width:870px;text-align:center;color:var(--white);font-size:14px;line-height:27px;font-weight:600}
.bio-note{position:absolute;left:0;top:200px;width:1200px;text-align:center;color:var(--white);font-size:14px;font-weight:600}
.org{position:absolute;top:258px;width:206px;height:77px;border:2px solid rgba(255,255,255,.85);color:var(--white);font-size:13px;font-weight:600;text-align:center;display:flex;align-items:center;justify-content:center;line-height:1.35;border-radius:3px}

/* services */
.service{position:absolute;width:220px;text-align:center}
.service-icon{width:108px;height:108px;border-radius:50%;margin:0 auto;border:2px solid var(--blue-deep);background:var(--white);box-shadow:0 6px 14px rgba(0,148,212,.15);display:flex;align-items:center;justify-content:center}
.service-icon.active{background:var(--teal);border:5px solid var(--white);box-shadow:0 0 0 2px var(--teal),0 6px 14px rgba(0,171,142,.25)}
.service-label{margin-top:18px;font-family:"Montserrat",sans-serif;font-size:14px;font-weight:700;color:var(--ink)}

/* difference */
.difference{position:absolute;left:0;top:2560px;width:1200px;height:665px;background:linear-gradient(90deg,var(--blue-mist) 0%,var(--blue-mist) 45%,#dbeef6 100%)}
.difference-photo{position:absolute;left:520px;top:0;width:680px;height:665px;background:radial-gradient(ellipse at 55% 25%,#f4f7f8 0%,#e2eef3 45%,rgba(233,246,251,0) 75%)}
.difference h2{position:absolute;left:140px;top:118px;font-family:"Montserrat",sans-serif;font-size:27px;line-height:31px;color:var(--ink);letter-spacing:.5px}
.difference h2 span{font-weight:400}
.difference h2 b{font-weight:700;display:block}
.difference-copy{position:absolute;left:140px;top:220px;width:575px;font-size:12.5px;line-height:17px;color:var(--text)}
.difference-copy p{margin-bottom:17px}
.review-card{position:absolute;left:778px;top:88px;width:305px;height:452px;background:var(--white);box-shadow:0 8px 24px rgba(0,60,90,.12);text-align:center}
.review-card .label{margin-top:30px;font-family:"Montserrat",sans-serif;font-size:13px;font-weight:700;color:var(--ink)}
.stars{color:#f5b400;font-size:17px;letter-spacing:3px}
.rating-row{margin-top:6px;display:flex;justify-content:center;align-items:center;gap:10px;font-weight:700;color:var(--ink);font-size:15px}
.count-row{margin-top:6px;font-size:11px;color:var(--text);display:flex;justify-content:center;align-items:center;gap:6px}
.count-dot{width:16px;height:16px;border-radius:50%;background:var(--blue-deep)}
.badge-row{margin-top:20px;display:flex;justify-content:center;gap:22px}
.badge{width:48px;height:16px;border-radius:3px;background:var(--blue-pale)}
.reviewer{margin:24px auto 0;display:flex;align-items:center;justify-content:center;gap:10px}
.avatar{width:50px;height:50px;border-radius:50%;background:linear-gradient(180deg,#c9b6a8,#8e7466)}
.reviewer .stars{font-size:14px}
.reviewer-name{font-family:"Montserrat",sans-serif;font-weight:700;font-size:13px;color:var(--ink);text-align:left}
.review-text{margin:12px 0 0 57px;width:185px;text-align:left;font-size:8.5px;line-height:10px;color:var(--text)}
.review-text a{color:var(--blue-deep);text-decoration:none}
.review-date{margin:14px 0 0 57px;text-align:left;font-size:9px;color:#8a969e}
.source-row{position:absolute;left:57px;bottom:40px;width:200px;display:flex;justify-content:space-between;align-items:center;font-size:9px}
.source-badge{width:74px;height:22px;border-radius:4px;background:var(--blue-pale)}
.arrow{position:absolute;top:258px;color:var(--blue-deep);font-size:22px;font-weight:700}

/* commitment */
.commitment{position:absolute;left:0;top:3225px;width:1200px;height:470px;background:var(--teal);overflow:hidden}
.commitment-photo{position:absolute;left:0;top:0;width:1200px;height:470px}
.commitment h2{position:absolute;left:606px;top:132px;font-family:"Montserrat",sans-serif;font-size:29px;line-height:40px;color:var(--white);letter-spacing:1px}
.commitment h2 b{font-weight:700;display:block}
.commitment h2 span{font-weight:400;display:block}
.commitment .rule{position:absolute;left:608px;top:222px;width:42px;height:3px;background:var(--white)}
.commitment .rule.thin{left:655px;width:4px}
.commitment .tagline{position:absolute;left:610px;top:244px;color:var(--white);font-size:22px;font-weight:400}
.commitment .outline-btn{left:615px;top:297px;width:210px;height:48px;font-size:12px}

/* footer info */
.footer-head{position:absolute;top:3762px;font-family:"Montserrat",sans-serif;font-size:17px;font-weight:700;color:var(--ink)}
.footer-rule{position:absolute;top:3793px;height:2px;background:var(--teal)}
.info-line{position:absolute;left:128px;display:flex;gap:12px;font-size:12.5px;line-height:18px;color:var(--text)}
.hours{position:absolute;left:460px;top:3826px;font-size:12.5px;color:var(--text)}
.hours div{display:flex;height:29.5px}
.hours span:first-child{width:114px}
.solid-btn{position:absolute;left:128px;top:3966px;width:208px;height:44px;background:var(--blue-deep);color:var(--white);font-family:"Montserrat",sans-serif;font-weight:700;font-size:12px;display:flex;align-items:center;justify-content:center;border-radius:2px}
.map{position:absolute;left:754px;top:3817px;width:307px;height:184px;border:1px solid #d5dde2;background:linear-gradient(135deg,#f1f3f4,#e6e9eb)}

/* bottom bar */
.bottom-bar{position:absolute;left:0;top:4075px;width:1200px;height:124px;border-top:1px solid #e3e8ea}
.bottom-links{position:absolute;top:34px;font-size:12px;color:var(--ink)}
.bottom-links span{position:absolute;white-space:nowrap}
.copyright{position:absolute;left:131px;top:60px;font-size:10px;color:var(--text)}
.social{position:absolute;left:922px;top:28px;display:flex;gap:6px}
.social i{width:24px;height:24px;border-radius:50%;background:var(--green);display:block}
</style>
</head>
<body>

<header class="site-header">
  <div class="brand"><span class="brand-dot"></span>Bright Harbor</div>
  <div class="phone">
    <svg width="22" height="22" viewBox="0 0 22 22"><circle cx="11" cy="11" r="11" fill="#0094D4"/><path d="M7.5 6.2c.5-.5 1.2-.4 1.5.1l1 1.6c.3.5.1 1-.3 1.3l-.6.4c.5 1.2 1.4 2.1 2.6 2.6l.4-.6c.3-.4.9-.6 1.3-.3l1.6 1c.5.3.6 1 .1 1.5l-.8.8c-.6.6-1.5.7-2.300.3-2.3-1.1-4-2.8-5.1-5.1-.4-.8-.3-1.7.3-2.3z" fill="#fff"/></svg>
    (555) 014-2260
  </div>
  <div class="pill schedule">Schedule Online</div>
  <div class="pill emergency">Emergency</div>
  <nav class="main-nav">
    <span style="left:316px">About Us ▾</span>
    <span style="left:413px">Services ▾</span>
    <span style="left:506px">Financing</span>
    <span style="left:606px">Testimonials</span>
    <span style="left:723px">New Patient Visit</span>
    <span style="left:869px">Specials</span>
    <span style="left:961px">Contact Us</span>
    <span style="left:1070px">Blog</span>
  </nav>
  <div class="nav-active-bar"></div>
</header>

<section class="hero">
  <h1 class="hero-title"><span class="light">CREATING</span><span class="bold">HEALTHIER SMILES</span></h1>
  <p class="hero-sub">With Advanced Technology and<br>Affordable Treatment</p>
  <div class="outline-btn">BOOK AN APPOINTMENT</div>
  <div class="hero-art" role="img" aria-label="Large faint illustration of teeth and dental instruments"></div>
</section>

<h2 class="section-title" style="top:740px"><span>MEET </span><b>OUR TEAM</b></h2>
<div class="title-rule" style="top:787px"></div>

<div class="member" style="left:135px">
  <div class="portrait" role="img" aria-label="Portrait photo of Dr. Ravi Mehra"></div>
  <h3>Meet Dr. Ravi Mehra</h3><p>General Dentist</p>
</div>
<div class="member" style="left:455px">
  <div class="portrait active" role="img" aria-label="Portrait photo of Dr. Anika Rao"></div>
  <h3>Dr. Anika Rao</h3><p>Endodontist</p>
</div>
<div class="member" style="left:775px">
  <div class="portrait" role="img" aria-label="Portrait photo of Dr. Priya Desai"></div>
  <h3>Dr. Priya Desai</h3><p>Cosmetic Dentist</p>
</div>

<div class="bio-pointer"></div>
<section class="bio-band">
  <p class="bio-text">Dr. Rao received her specialty training in Endodontics from Westbrook University. She graduated with a Master of Science in dentistry degree, in endodontics. She has practiced in Southern California for many years as a general dentist before specializing in endodontics and uses her experience to help her patients make the right decisions, regarding their treatment plans. She is gentle, compassionate and is committed to providing the optimum care for her patients.</p>
  <p class="bio-note">Dr. Rao is a member of several professional and service organizations, including:</p>
  <div class="org" style="left:187px">National Dental<br>Society (NDS)</div>
  <div class="org" style="left:397px">State Dental<br>Council (SDC)</div>
  <div class="org" style="left:607px">Global Dental<br>Forum (GDF)</div>
  <div class="org" style="left:817px">Harbor County Dental<br>Guild (HCDG)</div>
</section>

<h2 class="section-title" style="top:1758px"><span>OUR </span><b>SERVICES</b></h2>
<div class="title-rule" style="top:1805px"></div>

<svg width="0" height="0" style="position:absolute">
  <defs>
    <symbol id="tooth" viewBox="0 0 48 48"><path d="M14 8c-5 0-8 4-8 10 0 5 3 8 4 13 1 6 2 11 5 11 3 0 3-8 5-11 1-2 3-2 4-2s3 0 4 2c2 3 2 11 5 11 3 0 4-5 5-11 1-5 4-8 4-13 0-6-3-10-8-10-4 0-6 2-10 2s-6-2-10-2z" fill="none" stroke="currentColor" stroke-width="2.2" stroke-linejoin="round"/></symbol>
  </defs>
</svg>

<div class="service" style="left:126px;top:1874px"><div class="service-icon active"><svg width="50" height="50" style="color:#fff"><use href="#tooth"/></svg></div><div class="service-label">DENTAL IMPLANTS</div></div>
<div class="service" style="left:376px;top:1874px"><div class="service-icon"><svg width="50" height="50" style="color:#0094D4"><use href="#tooth"/></svg></div><div class="service-label">COSMETIC DENTISTRY</div></div>
<div class="service" style="left:607px;top:1874px"><div class="service-icon"><svg width="50" height="50" style="color:#0094D4"><use href="#tooth"/></svg></div><div class="service-label">BRACES</div></div>
<div class="service" style="left:847px;top:1874px"><div class="service-icon"><svg width="50" height="50" style="color:#0094D4"><use href="#tooth"/></svg></div><div class="service-label">CROWNS</div></div>

<div class="service" style="left:125px;top:2089px"><div class="service-icon"><svg width="50" height="50" style="color:#0094D4"><use href="#tooth"/></svg></div><div class="service-label">BRIDGE</div></div>
<div class="service" style="left:372px;top:2089px"><div class="service-icon"><svg width="50" height="50" style="color:#0094D4"><use href="#tooth"/></svg></div><div class="service-label">EXTRACTIONS</div></div>
<div class="service" style="left:603px;top:2089px"><div class="service-icon"><svg width="50" height="50" style="color:#0094D4"><use href="#tooth"/></svg></div><div class="service-label">GUM DISEASE</div></div>
<div class="service" style="left:847px;top:2089px"><div class="service-icon"><svg width="50" height="50" style="color:#0094D4"><use href="#tooth"/></svg></div><div class="service-label">ROOT CANAL</div></div>

<div class="service" style="left:129px;top:2306px"><div class="service-icon"><svg width="50" height="50" style="color:#0094D4"><use href="#tooth"/></svg></div><div class="service-label">DENTURES</div></div>
<div class="service" style="left:371px;top:2306px"><div class="service-icon"><svg width="50" height="50" style="color:#0094D4"><use href="#tooth"/></svg></div><div class="service-label">EMERGENCY DENTISTRY</div></div>
<div class="service" style="left:607px;top:2306px"><div class="service-icon"><svg width="50" height="50" style="color:#0094D4"><use href="#tooth"/></svg></div><div class="service-label">VENEERS</div></div>
<div class="service" style="left:843px;top:2306px"><div class="service-icon"><svg width="50" height="50" style="color:#0094D4"><use href="#tooth"/></svg></div><div class="service-label">CLEAR ALIGNERS</div></div>

<section class="difference">
  <div class="difference-photo" role="img" aria-label="Soft background photo of a smiling patient"></div>
  <h2><span>EXPERIENCE THE BRIGHT</span><b>HARBOR DIFFERENCE</b></h2>
  <div class="difference-copy">
    <p>Your smile is our #1 priority. At Bright Harbor, we provide affordable and expert dental solutions. Whether you are looking for a family dentist or have any emergency such as needing a root canal in Lakemont, we are here for you! We want to keep your teeth healthy inside and out. We don't just clean teeth and send you on your way, we want to get to know you.</p>
    <p>We accept most HMO and PPO insurances. We offer various financing options through CarePay, LendWell and In-House Plans.</p>
    <p>To constantly strive to achieve the highest level of skills and modern techniques and equipment so we can provide our patients with the best that Dentistry has to offer at our dental office in Lakemont, Harbor County, CA.</p>
    <p>We provide patients with the best experience you can find in all of Southern California. We provide a comfortable and friendly atmosphere to shatter any fears you may have. We supply you with all the information on your dental health options so you can feel comfortable in the choices you make, whether it's a routine check-up or dental implants in Lakemont.</p>
    <p>We are available for Emergency and Walk-ins.</p>
  </div>
  <div class="review-card">
    <div class="label">AVERAGE RATING</div>
    <div class="rating-row"><span class="stars">★★★★★</span>4.9</div>
    <div class="count-row"><span class="count-dot"></span>126 Reviews</div>
    <div class="badge-row"><span class="badge"></span><span class="badge"></span><span class="badge"></span></div>
    <div class="reviewer">
      <div class="avatar" role="img" aria-label="Reviewer profile photo"></div>
      <div><div class="stars">★★★★★</div><div class="reviewer-name">Laura Bennett</div></div>
    </div>
    <p class="review-text">Dr. Mehra and her staff are awesome! Everyone is so nice and pleasant. I always have a great experience! I don't ever feel rushed and time is taken to answer questions and make sure we are on the same page! This office i... <a>more</a></p>
    <p class="review-date">26 February, 2021</p>
    <div class="source-row"><span>Source:</span><span class="source-badge"></span></div>
    <span class="arrow" style="left:24px">‹</span>
    <span class="arrow" style="right:24px">›</span>
  </div>
</section>

<section class="commitment">
  <svg class="commitment-photo" viewBox="0 0 1200 470" role="img" aria-label="Photo of a smiling patient during a dental check-up">
    <defs>
      <linearGradient id="photoTone" x1="0" y1="0" x2="1" y2="1">
        <stop offset="0" stop-color="#e9e2dc"/><stop offset=".6" stop-color="#d8c8bc"/><stop offset="1" stop-color="#b9c7cf"/>
      </linearGradient>
    </defs>
    <path d="M0 0H620C540 90 500 240 500 470H0Z" fill="url(#photoTone)"/>
  </svg>
  <h2><b>COMMITTED TO EXCELLENCE</b><span>IN ORAL HEALTH CARE</span></h2>
  <div class="rule"></div><div class="rule thin"></div>
  <p class="tagline">Free Exam and X-Rays for New Patients</p>
  <div class="outline-btn">BOOK AN APPOINTMENT</div>
</section>

<div class="footer-head" style="left:128px">BRIGHT HARBOR</div>
<div class="footer-rule" style="left:128px;width:190px"></div>
<div class="footer-head" style="left:460px">OFFICE HOURS</div>
<div class="footer-rule" style="left:460px;width:150px"></div>
<div class="footer-head" style="left:749px">OUR LOCATION</div>
<div class="footer-rule" style="left:754px;width:300px"></div>

<div class="info-line" style="top:3822px">
  <svg width="16" height="20" viewBox="0 0 16 20"><path d="M8 0C3.6 0 0 3.4 0 7.7 0 13 8 20 8 20s8-7 8-12.3C16 3.4 12.4 0 8 0z" fill="#0094D4"/><circle cx="8" cy="7.5" r="3" fill="#fff"/></svg>
  <span>48 Harbor View Rd., Suite B<br>Lakemont, CA 90001</span>
</div>
<div class="info-line" style="top:3884px">
  <svg width="16" height="16" viewBox="0 0 16 16"><path d="M3 1.5c.5-.5 1.3-.4 1.6.2l1.2 2c.3.5.1 1.1-.3 1.4l-.8.6c.7 1.6 1.9 2.8 3.5 3.5l.6-.8c.3-.4 1-.6 1.4-.3l2 1.2c.6.3.7 1.1.2 1.6l-1 1c-.7.7-1.8.9-2.7.4C5.6 11 4 9.4 2.6 6.3c-.5-.9-.3-2 .4-2.7z" fill="none" stroke="#0094D4" stroke-width="1.4"/></svg>
  <span>Call Us: (555) 014-2260</span>
</div>
<div class="info-line" style="top:3914px">
  <svg width="16" height="16" viewBox="0 0 16 16"><rect x="1" y="3" width="14" height="10" fill="#0094D4"/><path d="M1 3l7 6 7-6" fill="none" stroke="#fff" stroke-width="1.3"/></svg>
  <span>hello@mybrightharbor.example</span>
</div>
<div class="solid-btn">BOOK AN APPOINTMENT</div>

<div class="hours">
  <div><span>Monday:</span><span>10AM–7PM</span></div>
  <div><span>Tuesday:</span><span>10AM–7PM</span></div>
  <div><span>Wednesday:</span><span>9AM–6PM</span></div>
  <div><span>Thursday:</span><span>9AM–6PM</span></div>
  <div><span>Friday:</span><span>9AM–5PM</span></div>
  <div><span>Saturday:</span><span>9AM–1PM</span></div>
</div>

<div class="map" role="img" aria-label="Street map showing the office location"></div>

<footer class="bottom-bar">
  <div class="bottom-links">
    <span style="left:131px">About Us</span>
    <span style="left:218px">Services</span>
    <span style="left:301px">Financing</span>
    <span style="left:390px">Testimonials</span>
    <span style="left:495px">New Patient Visit</span>
    <span style="left:627px">Specials</span>
    <span style="left:708px">Contact Us</span>
    <span style="left:806px">Blog</span>
  </div>
  <p class="copyright">2021 Bright Harbor &nbsp;|&nbsp; All Rights Reserved</p>
  <div class="social"><i></i><i></i><i></i><i></i><i></i></div>
</footer>

</body>
</html>
```